Verlindo Magician

I want the business card for my business to give to people who watch that later I will be employed to show magic here is my website http://www.balsamomagicien.com/I want the interesting design , i am very opened for formal and informal, I watch a lot of design so don't stick to the common shape and form but i hope it can also be produced the thing to write on will be the same as in picture that i will upload , i also will upload the logo for you that so can be easy to useDenis CostilleMagicianMAGICIAN VERLINDO 17 rue des Tilleuls - 25000 BESANÇON contact@verlindoillusions.example tel. 0381 946 157 tel. 0674 219 503

```html
<!DOCTYPE html>
<html lang="fr">
<head>
<meta charset="utf-8">
<title>Verlindo Magician – Business Card</title>
<link rel="stylesheet" href="https://fonts.googleapis.com/css2?family=Josefin+Sans:wght@300;400&family=Arimo:wght@400;700&display=swap">
<style>
  :root {
    --backdrop: #5a5a5a;
    --card: #ffffff;
    --ink: #1a1a1a;
    --accent: #e4262b;
    --art-dark: #111111;
    --art-light: #8a8a8a;
  }
  * { box-sizing: border-box; margin: 0; padding: 0; }
  html, body {
    width: 1200px; height: 900px; overflow: hidden;
    background: var(--backdrop);
  }
  .stage { position: relative; width: 1200px; height: 900px; }
  .card {
    position: absolute; left: 338px;
    width: 524px; height: 299px;
    background: linear-gradient(180deg, #f6f6f6 0%, var(--card) 45%);
    box-shadow: 0 10px 24px rgba(0,0,0,.35);
    color: var(--ink);
  }
  .card--front { top: 129px; }
  .card--back { top: 472px; background: var(--card); }

  .portrait {
    position: absolute;
    background: linear-gradient(160deg, var(--art-light) 0%, var(--art-dark) 55%);
    border-radius: 40% 40% 18% 18% / 30% 30% 12% 12%;
  }
  .card--front .portrait { left: 388px; top: 36px; width: 99px; height: 126px; }
  .card--back .portrait { left: 200px; top: 37px; width: 134px; height: 168px; }

  .holder-name {
    position: absolute; left: 39px; top: 108px;
    font-family: "Josefin Sans", sans-serif; font-weight: 300;
    font-size: 22px; letter-spacing: .5px; text-transform: uppercase;
  }
  .holder-name .given { font-weight: 400; margin-right: 6px; }
  .holder-role {
    position: absolute; left: 39px; top: 134px;
    font-family: "Arimo", sans-serif; font-size: 12.5px; letter-spacing: .4px;
  }
  .rule {
    position: absolute; left: 39px; top: 169px;
    width: 33px; height: 2px; background: var(--accent);
  }
  .contact {
    position: absolute; left: 39px; top: 185px;
    font-family: "Arimo", sans-serif; font-size: 12.5px;
    line-height: 20.4px; letter-spacing: .3px; list-style: none;
  }
  .contact .label { color: var(--accent); font-weight: 700; margin-right: 3px; }
  .contact .gap { margin-left: 10px; }

  .wordmark {
    position: absolute; left: 0; right: 0; top: 206px;
    text-align: center;
    font-family: "Josefin Sans", sans-serif; font-weight: 300;
    font-size: 30px; letter-spacing: 1px;
  }
</style>
</head>
<body>
<main class="stage">
  <section class="card card--front">
    <div class="portrait" role="img" aria-label="Black and white illustration of the magician in a dark jacket holding a playing card"></div>
    <h1 class="holder-name"><span class="given">Marc</span>Ravoulet</h1>
    <p class="holder-role">Magician</p>
    <div class="rule"></div>
    <ul class="contact">
      <li>MAGICIAN VERLINDO</li>
      <li>17 rue des Tilleuls - 25000 BESANÇON</li>
      <li><span class="label">t.</span>0381 946 157 / 0674 219 503<span class="gap"><span class="label">e.</span>contact@verlindoillusions.example</span></li>
      <li><span class="label">w.</span>www.verlindoillusions.example</li>
    </ul>
  </section>

  <section class="card card--back">
    <div class="portrait" role="img" aria-label="Large black and white illustration of the magician holding a playing card to his chest"></div>
    <p class="wordmark">VERLINDO</p>
  </section>
</main>
</body>
</html>
```